Seeking for catalogue design -for Event Mgmt company

Need to be creative and striking and images to be more enhanced.
The items in the catalogue have to be layout well and easy to read.
Cover and background of catalogue needs to be striking but not overpowering the items.
Catologue needs to be able to put up on website and able to read on mobile.
Font used must be easily readable and not too small.

Target Market(s)

Business and Public Sectors

Industry/Entity Type

Event Planning

Colors

Designer to choose colors to be used in the design.

Requirements
Must have
• Not too many colors but must be creative
Nice to have
• See that the images of items in catalogue have better layout
Should not have
• Not to be so messy

```html
<!DOCTYPE html>
<html lang="en">
<head>
<meta charset="utf-8">
<title>Lumera Events – Carnival Catalogue p.10</title>
<link href="https://fonts.googleapis.com/css2?family=Cabin:wght@600&family=Open+Sans:wght@400;700&display=swap" rel="stylesheet">
<style>
  :root{
    --teal-light:#ade8e3;
    --teal-mid:#7fcfd3;
    --teal-deep:#6fc2c6;
    --grey-shadow:#e4e4e4;
    --brand-box:#a19a97;
    --frame:#7a7a7a;
    --ink:#3d3d3d;
    --body:#4a4a4a;
    --white:#ffffff;
  }
  *{margin:0;padding:0;box-sizing:border-box}
  html,body{width:848px;height:1200px;overflow:hidden;background:var(--white)}
  .page{position:relative;width:848px;height:1200px;overflow:hidden;background:var(--white);font-family:"Open Sans",sans-serif;color:var(--body)}
  .backdrop{position:absolute;inset:0}
  .brand{position:absolute;left:0;top:0;width:197px;height:65px;background:var(--brand-box);box-shadow:4px 4px 5px rgba(0,0,0,.25);color:var(--white);text-align:center}
  .brand-name{font-family:"Cabin",sans-serif;font-weight:600;font-size:34px;letter-spacing:1px;line-height:1;padding-top:9px}
  .brand-sub{font-family:"Cabin",sans-serif;font-weight:600;font-size:8px;letter-spacing:1px;margin-top:3px}
  .page-number{position:absolute;right:8px;top:4px;font-family:"Cabin",sans-serif;font-weight:600;font-size:34px;color:var(--white);letter-spacing:1px}
  .item{position:absolute;width:260px;text-align:center}
  .item-title{font-family:"Cabin",sans-serif;font-weight:600;font-size:16.5px;letter-spacing:.5px;color:var(--ink);height:24px}
  .item-photo{width:173px;height:168px;margin:11px auto 0;border:4px solid var(--frame);box-shadow:5px 5px 5px rgba(0,0,0,.25)}
  .item-info{margin-top:28px;font-size:15px;line-height:19px;color:var(--body)}
  .footer{position:absolute;left:0;top:1127px;width:848px;border-top:1px solid #555;padding:8px 0 0 25px;font-weight:700;font-size:14.5px;line-height:18.5px;letter-spacing:.4px;color:var(--ink)}
</style>
</head>
<body>
<div class="page">
  <svg class="backdrop" width="848" height="1200" viewBox="0 0 848 1200" aria-hidden="true">
    <defs>
      <linearGradient id="deepFill" x1="0" y1="0" x2="0" y2="1">
        <stop offset="0" stop-color="var(--teal-mid)"/>
        <stop offset="1" stop-color="var(--teal-deep)"/>
      </linearGradient>
    </defs>
    <circle cx="848" cy="30" r="303" fill="var(--grey-shadow)"/>
    <circle cx="842" cy="25" r="300" fill="var(--teal-light)"/>
    <circle cx="848" cy="80" r="245" fill="var(--teal-mid)"/>
    <circle cx="238" cy="868" r="535" fill="var(--grey-shadow)"/>
    <circle cx="225" cy="865" r="540" fill="var(--teal-light)"/>
    <circle cx="250" cy="950" r="460" fill="url(#deepFill)"/>
  </svg>

  <div class="brand">
    <div class="brand-name">LUMERA</div>
    <div class="brand-sub">LUMERA EVENTS PTE LTD</div>
  </div>
  <div class="page-number">10</div>

  <div class="item" style="left:6px;top:104px">
    <div class="item-title">CARNIVAL EQUIPMENT</div>
    <div class="item-photo" role="img" aria-label="Large ball pit with coloured foam walls in a mall" style="background:linear-gradient(160deg,#d9d4cf 0%,#c8c0b8 35%,#5f8fc2 55%,#e3b52f 75%,#d6342e 100%)"></div>
    <div class="item-info">Large Ball Pit<br>4m by 2.5m<br>Indoor only (8000 balls)<br>SGD$1700</div>
  </div>

  <div class="item" style="left:306px;top:104px">
    <div class="item-title">CARNIVAL EQUIPMENT</div>
    <div class="item-photo" role="img" aria-label="Giant ball pit full of coloured balls" style="margin-top:8px;background:linear-gradient(165deg,#b8302d 0%,#8fbf6a 20%,#e2c23e 45%,#5aa2d6 60%,#3fb548 75%,#d8312b 100%)"></div>
    <div class="item-info" style="margin-top:26px">Giant Ball Pit<br>5m by 4m<br>Indoor only (16000 balls)<br>SGD$2700</div>
  </div>

  <div class="item" style="left:598px;top:104px">
    <div class="item-title">CARNIVAL EQUIPMENT</div>
    <div class="item-photo" role="img" aria-label="Mega inflatable ball pit in a mall atrium" style="background:linear-gradient(175deg,#6b5a4c 0%,#a58b73 40%,#d9b792 62%,#2d62c4 85%,#1f4fb0 100%)"></div>
    <div class="item-info" style="margin-top:23px">Mega Ball Pit<br>12m by 6m<br>Indoor only (38000 balls)<br>SGD$5200</div>
  </div>

  <div class="item" style="left:1px;top:457px">
    <div class="item-title">GAME PRIZES</div>
    <div class="item-photo" role="img" aria-label="Assorted keychain game prizes on cards" style="background:linear-gradient(150deg,#f4c8ae 0%,#eea583 50%,#e9a17f 100%)"></div>
    <div class="item-info" style="width:260px;margin-left:-3px;margin-top:26px">Assorted Game Prizes<br>$1/pc (min 100pcs)<br>Only available with Game Stalls<br>$0.70 for 1000pcs and above</div>
  </div>

  <div class="item" style="left:304px;top:457px">
    <div class="item-title">SOFT TOYS</div>
    <div class="item-photo" role="img" aria-label="Small soft toys in a claw machine" style="background:linear-gradient(170deg,#c9c6d8 0%,#e9c14a 40%,#d9b53a 60%,#c94f73 85%,#555 100%)"></div>
    <div class="item-info" style="margin-top:22px">Small Soft Toys<br>$7/piece</div>
  </div>

  <div class="item" style="left:605px;top:457px">
    <div class="item-title">SOFT TOYS</div>
    <div class="item-photo" role="img" aria-label="Large soft toys hanging at a carnival game stall" style="background:linear-gradient(180deg,#e7e7ea 0%,#d9a7a2 30%,#d7332c 55%,#c42924 100%)"></div>
    <div class="item-info" style="margin-top:25px;margin-left:-16px">Large Soft Toys<br>$20/piece</div>
  </div>

  <div class="footer">
    *Size stated above is estimated only.<br>
    *Rates include Delivery, Set up, Dismantle and Collection of the equipments.<br>
    *The more items or more days rented, we may be able to quote a much better discounted package rate
  </div>
</div>
</body>
</html>
```